Business Card Design (NEW FILES)

ATTENTION: New vector files are available. Please update your design to reflect/use the new (better resolution) logo images.

Seeking a unique and professional business card design for a commercial drone photography/videography business. The layout should feature
the logo (attached) and include the following information:
Owen Tarrick
614-502-7738
www.skylarkreelworks.example
NRD Certified Remote Pilot

Owen Tarrick

```html
<!DOCTYPE html>
<html lang="en">
<head>
<meta charset="utf-8">
<title>Skylark Reelworks – Business Card</title>
<link href="https://fonts.googleapis.com/css2?family=Open+Sans:ital,wght@0,400;0,600;0,700;1,400&display=swap" rel="stylesheet">
<style>
  :root {
    --backdrop: #232323;
    --card-navy: #161a45;
    --emboss-navy: #222a6a;
    --accent-orange: #e7823a;
    --text-white: #ffffff;
  }
  * { margin: 0; padding: 0; box-sizing: border-box; }
  html, body {
    width: 1200px; height: 780px; overflow: hidden;
    background: var(--backdrop);
    font-family: "Open Sans", Arial, sans-serif;
  }
  .stage {
    position: relative; width: 1200px; height: 780px;
  }
  .card {
    position: absolute; top: 236px;
    width: 540px; height: 309px;
    background: var(--card-navy);
    border-radius: 3px;
    box-shadow: 0 14px 30px rgba(0,0,0,.45);
    overflow: hidden;
  }
  .card--front { left: 30px; }
  .card--back { left: 630px; }

  /* front */
  .brand {
    position: absolute; left: 40px; top: 62px; width: 200px;
    display: flex; align-items: center; justify-content: center; gap: 8px;
    color: var(--text-white); font-weight: 600; font-size: 19px; letter-spacing: .5px;
  }
  .brand__dot {
    width: 14px; height: 14px; border-radius: 50%;
    background: var(--accent-orange); flex: none;
  }
  .divider {
    position: absolute; left: 258px; top: 62px;
    width: 1.5px; height: 185px; background: var(--accent-orange);
  }
  .credentials {
    position: absolute; left: 0; width: 300px; top: 258px;
    text-align: center; color: var(--text-white);
    font-style: italic; font-size: 12.5px;
  }
  .person {
    position: absolute; left: 282px; top: 108px; color: var(--text-white);
  }
  .person__name { font-weight: 700; font-size: 23px; line-height: 1.1; }
  .person__first { color: var(--accent-orange); }
  .person__role { font-size: 11px; margin-top: 2px; }
  .contacts { list-style: none; margin-top: 16px; }
  .contacts li {
    display: flex; align-items: center; gap: 8px;
    font-size: 12px; line-height: 21px;
  }
  .contacts svg { width: 12px; height: 12px; flex: none; }

  /* back */
  .brand--emboss {
    left: 0; right: 0; top: 0; bottom: 0; width: auto;
    color: var(--emboss-navy); font-size: 34px; gap: 14px;
  }
  .brand--emboss .brand__dot {
    width: 26px; height: 26px; background: var(--emboss-navy);
  }
</style>
</head>
<body>
<main class="stage">
  <section class="card card--front" aria-label="Business card front">
    <div class="brand"><span class="brand__dot"></span>Skylark Reelworks</div>
    <div class="divider"></div>
    <p class="credentials">NRD Certified Remote Pilot Fully Insured</p>
    <div class="person">
      <h1 class="person__name"><span class="person__first">Owen</span> Tarrick</h1>
      <p class="person__role">Owner</p>
      <ul class="contacts">
        <li>
          <svg viewBox="0 0 24 24" aria-hidden="true"><path fill="#e7823a" d="M6.6 10.8a15 15 0 0 0 6.6 6.6l2.2-2.2a1 1 0 0 1 1-.25 11.4 11.4 0 0 0 3.6.57 1 1 0 0 1 1 1V20a1 1 0 0 1-1 1A17 17 0 0 1 3 4a1 1 0 0 1 1-1h3.5a1 1 0 0 1 1 1c0 1.25.2 2.45.57 3.57a1 1 0 0 1-.25 1z"/></svg>
          614-502-7738
        </li>
        <li>
          <svg viewBox="0 0 24 24" aria-hidden="true"><circle cx="12" cy="12" r="9" fill="none" stroke="#e7823a" stroke-width="2.4"/><path d="M3 12h18M12 3c3 3 3 15 0 18M12 3c-3 3-3 15 0 18" fill="none" stroke="#e7823a" stroke-width="1.8"/></svg>
          www.skylarkreelworks.example
        </li>
        <li>
          <svg viewBox="0 0 24 24" aria-hidden="true"><rect x="2" y="5" width="20" height="14" rx="2" fill="#e7823a"/><path d="M3 6l9 7 9-7" fill="none" stroke="#161a45" stroke-width="1.8"/></svg>
          info@skylarkreelworks.example
        </li>
      </ul>
    </div>
  </section>

  <section class="card card--back" aria-label="Business card back">
    <div class="brand brand--emboss"><span class="brand__dot"></span>Skylark Reelworks</div>
  </section>
</main>
</body>
</html>
```